​Silver Harbor Rhythm provides personal, friendly service in a fun and high energy environment. We are based in Vermont.

We would like a card that appeals to a wide range of audiences as we do a wide range of events. Please feel free to check out our website silverharborrhythm.net for inspiration.

Target Market(s)

weddings, corporate, birthday parties, colleges

Industry/Entity Type

Business

Contact Information for Business Card

Silver Harbor Rhythm
Providing Entertainment For All Occasions
555 274 9160
silverharborrhythm@mailnest.net
silverharborrhythm.net

```html
<!DOCTYPE html>
<html lang="en">
<head>
<meta charset="utf-8">
<title>Silver Harbor Rhythm – Business Card</title>
<link rel="stylesheet" href="https://fonts.googleapis.com/css2?family=Open+Sans:wght@400;600;700&display=swap">
<style>
  :root {
    --bg: #e9e6e1;
    --card: #ffffff;
    --green: #2f6a1c;
    --maroon: #3f1a22;
    --ink: #3a3a3a;
    --muted: #666666;
    --rule: #c9c9c9;
  }
  * { box-sizing: border-box; margin: 0; padding: 0; }
  html, body { width: 1200px; height: 829px; overflow: hidden; }
  body {
    background: var(--bg);
    font-family: "Open Sans", Arial, sans-serif;
    position: relative;
  }
  .card {
    position: absolute;
    width: 520px;
    height: 297px;
    background: var(--card);
    box-shadow: 0 6px 18px rgba(0,0,0,0.18);
    overflow: hidden;
  }
  .card--front { left: 50px; top: 266px; }
  .card--back { left: 630px; top: 266px; }

  .wave { position: absolute; inset: 0; width: 100%; height: 100%; }

  .brand {
    position: absolute;
    display: flex;
    align-items: center;
    gap: 8px;
  }
  .brand__mark {
    width: 14px; height: 14px;
    background: var(--green);
    flex: none;
  }
  .brand__name {
    color: var(--green);
    font-weight: 700;
    text-transform: uppercase;
    letter-spacing: 0.5px;
    white-space: nowrap;
  }
  .card--front .brand { left: 30px; top: 112px; width: 250px; }
  .card--front .brand__mark { width: 12px; height: 12px; }
  .card--front .brand__name { font-size: 15px; }

  .contact {
    position: absolute;
    left: 300px;
    top: 26px;
    padding-left: 12px;
    border-left: 1px solid var(--rule);
    color: var(--ink);
    font-size: 11px;
    line-height: 1.6;
  }
  .contact__name { color: var(--green); font-weight: 700; font-size: 14px; line-height: 1.2; }
  .contact__title { font-size: 11.5px; margin-bottom: 4px; }
  .contact__row { display: flex; align-items: center; gap: 6px; }
  .contact__icon { width: 11px; height: 11px; flex: none; }
  .contact__address { margin-top: 4px; color: var(--muted); }

  .card--back .brand {
    left: 0; right: 0; top: 118px;
    justify-content: center;
  }
  .card--back .brand__name { font-size: 26px; }
  .card--back .brand__mark { width: 18px; height: 18px; }
  .website {
    position: absolute;
    left: 0; right: 0; top: 178px;
    text-align: center;
    color: var(--ink);
    font-size: 17px;
    letter-spacing: 0.5px;
  }
</style>
</head>
<body>

  <section class="card card--front" aria-label="Business card front">
    <svg class="wave" viewBox="0 0 520 297" aria-hidden="true">
      <path fill="var(--maroon)" d="M95,297 C250,287 385,240 520,184 L520,297 Z"/>
      <path fill="var(--green)" d="M0,250 C180,292 340,250 520,152 L520,174 C360,252 200,297 60,297 L0,297 Z"/>
    </svg>

    <div class="brand">
      <span class="brand__mark"></span>
      <span class="brand__name">Silver Harbor Rhythm</span>
    </div>

    <div class="contact">
      <div class="contact__name">Your Name</div>
      <div class="contact__title">Title</div>
      <div class="contact__row">
        <svg class="contact__icon" viewBox="0 0 12 12" aria-hidden="true"><circle cx="6" cy="6" r="6" fill="var(--ink)"/><path d="M4 3.2l1 1.3-.6.7c.4.8 1 1.4 1.8 1.8l.7-.6 1.3 1-.6 1.1C5.7 8.2 3.8 6.3 3.5 3.8z" fill="#fff"/></svg>
        <span>555 274 9160</span>
      </div>
      <div class="contact__row">
        <svg class="contact__icon" viewBox="0 0 12 12" aria-hidden="true"><circle cx="6" cy="6" r="6" fill="var(--ink)"/><rect x="3" y="4" width="6" height="4.2" fill="#fff"/><path d="M3 4l3 2.3L9 4" stroke="var(--ink)" stroke-width=".7" fill="none"/></svg>
        <span>silverharborrhythm@mailnest.net</span>
      </div>
      <div class="contact__row">
        <svg class="contact__icon" viewBox="0 0 12 12" aria-hidden="true"><circle cx="6" cy="6" r="6" fill="var(--ink)"/><circle cx="6" cy="6" r="3" fill="none" stroke="#fff" stroke-width=".8"/><path d="M3 6h6M6 3v6" stroke="#fff" stroke-width=".6"/></svg>
        <span>www.silverharborrhythm.net</span>
      </div>
      <div class="contact__address">
        Street Name, City Name<br>Zip Code-00000
      </div>
    </div>
  </section>

  <section class="card card--back" aria-label="Business card back">
    <div class="brand">
      <span class="brand__mark"></span>
      <span class="brand__name">Silver Harbor Rhythm</span>
    </div>
    <div class="website">www.silverharborrhythm.net</div>
  </section>

</body>
</html>
```